Business Cards for a law firm

Business cards for our law firm. Use our silhoette logo and OAK PARTNERS - check our website (www.oakpartners.example)

Contact Information for Business Card

our silhouette logo, OAK PARTNERS, 800-555-0147, Dorian Pemberton, dorian@oakpartners.example

Requirements
Must have
• our silhouette logo, OAK PARTNERS, 800-555-0147, Dorian Pemberton, dorian@oakpartners.example

```html
<!DOCTYPE html>
<html lang="en">
<head>
<meta charset="utf-8">
<title>Oak Partners – Business Cards</title>
<link href="https://fonts.googleapis.com/css2?family=Montserrat:wght@500;600&family=Open+Sans:wght@400&display=swap" rel="stylesheet">
<style>
  :root {
    --backdrop: #2c2f34;
    --navy: #1e3473;
    --navy-deep: #1b2f68;
    --paper: #ffffff;
    --icon-1: #3a5a9e;
    --icon-2: #2f8fd6;
    --icon-3: #2b6a9c;
    --icon-4: #2a4d73;
  }
  * { margin: 0; padding: 0; box-sizing: border-box; }
  html, body {
    width: 1200px; height: 985px; overflow: hidden;
    background: var(--backdrop);
  }
  .stage {
    position: relative; width: 1200px; height: 985px;
    display: flex; align-items: center; justify-content: center; gap: 40px;
  }
  .card {
    position: relative; width: 540px; height: 309px;
    border-radius: 18px; overflow: hidden;
  }
  .card--front { background: var(--paper); color: var(--navy); }
  .card--back { background: var(--navy-deep); color: var(--paper); }

  .logo-mark {
    position: absolute; background: var(--navy);
  }
  .card--front .logo-mark { left: 52px; top: 40px; width: 150px; height: 150px; }

  .firm-name {
    position: absolute;
    font-family: "Montserrat", sans-serif; font-weight: 600;
    letter-spacing: 3px; white-space: nowrap;
  }
  .card--front .firm-name { left: 222px; top: 112px; font-size: 30px; }
  .divider {
    position: absolute; left: 272px; top: 158px; width: 122px; height: 2px;
    background: var(--navy);
  }
  .person {
    position: absolute; left: 258px; top: 172px;
    font-family: "Montserrat", sans-serif; font-weight: 500;
    font-size: 15px; letter-spacing: 1px;
  }
  .contact {
    position: absolute; left: 286px; top: 196px;
    font-family: "Open Sans", sans-serif; font-size: 12px; line-height: 18px;
  }
  .web-band {
    position: absolute; left: 0; top: 244px; width: 218px; height: 30px;
    background: var(--navy); color: var(--paper);
    font-family: "Open Sans", sans-serif; font-size: 11px; letter-spacing: 1.5px;
    display: flex; align-items: center; padding-left: 20px;
  }
  .social {
    position: absolute; left: 228px; top: 246px; display: flex; gap: 12px;
  }
  .social span { display: block; width: 26px; height: 26px; border-radius: 3px; }
  .social .s1 { background: var(--icon-1); }
  .social .s2 { background: var(--icon-2); }
  .social .s3 { background: var(--icon-3); }
  .social .s4 { background: var(--icon-4); }

  .card--back .logo-mark { left: 98px; top: 96px; width: 44px; height: 44px; background: var(--paper); }
  .card--back .firm-name { left: 156px; top: 100px; font-size: 30px; }
</style>
</head>
<body>
<main class="stage">
  <section class="card card--front" aria-label="Business card front">
    <div class="logo-mark" role="img" aria-label="Oak Partners logo mark"></div>
    <h1 class="firm-name">OAK PARTNERS</h1>
    <div class="divider"></div>
    <p class="person">DORIAN PEMBERTON</p>
    <p class="contact">800-555-0147<br>dorian@oakpartners.example</p>
    <div class="web-band">WWW.OAKPARTNERS.EXAMPLE</div>
    <div class="social" aria-label="Social profiles">
      <span class="s1"></span><span class="s2"></span><span class="s3"></span><span class="s4"></span>
    </div>
  </section>
  <section class="card card--back" aria-label="Business card back">
    <div class="logo-mark" role="img" aria-label="Oak Partners logo mark"></div>
    <h2 class="firm-name">OAK PARTNERS</h2>
  </section>
</main>
</body>
</html>
```